wardrobe/costume stylist needs good business card for own business

Hi:)

I'm wanting a business card for my company. I am a freelance stylist.

I do wardrobe/costume stylist to TV commercials; Films; Fashion and Lifestyle shoots.

I'd like a design based around my name Rosalind Parfrey written nicely, maybe a colour? Up to you?!

I've attached a couple of images of business cards I like
.... be creative and have fun!

Thank you :)

Reason: I was trying to get my new business card ready for before I headed overseas Friday morning but I don't think that was realistic so I'd like to extend the deadline to give time to the project. Thank you

Hi designers:) Thank you for all your designs, I've extended the deadline until Sunday, so there's a bit more time. I've attached 3 pictures of business cards which I quite like, please take a look to see if it can be of help in your process. I like the pale plain or patterned background with dark font and the dark plain or patterned background with the pale font the motifs the feminine fonts the plain fonts I like the idea of playing with a circle or some shape on one side of the card with my name or initials as in the picture I have on my post could you play around with this idea a bit please? Thank you all for the work you've done :) Rosa

Hi I am working overseas til Saturday night sorry for no feedback until I teturn Thanks :) Rosa

Hi designers, Thank you all so much for submitting your designs, I really appreciate your input into my project :) I'm sorry I didn't get to respond to some comments, and give feedback. I didn't back from being away until later than I expected, and the deadline had passed then, so apologies. Thanks to you all again for all your really good designs :) Rosa

Target Market(s)

I am a freelance stylist my target audience is producers, production companies, photographers, directors...

Industry/Entity Type

Business

Requirements
Must have
• Rosalind Parfrey
Stylist or Wardrobe Stylist

email rosaparfrey@mailbox-example.co.nz
Mobile 0218467193

(Don't have to use the words 'email' and 'mobile')
Nice to have
• Would like it to be double sided
Like B & W
Like pale colour background with dark font or white font
Like dark colour background with pale font
Should not have
• I would prefer it not to incorporate pictures

```html
<!DOCTYPE html>
<html lang="en">
<head>
<meta charset="utf-8">
<title>Rosalind Parfrey — Wardrobe Stylist Business Card</title>
<link rel="stylesheet" href="https://fonts.googleapis.com/css2?family=Almendra:wght@700&family=Poiret+One&display=swap">
<style>
  :root {
    --page-bg: #ffffff;
    --mint: #b4e0cc;
    --mint-light: #d6efe3;
    --ink: #111111;
    --card-dark: #1c1c1c;
    --card-dark-edge: #050505;
  }
  * { margin: 0; padding: 0; box-sizing: border-box; }
  html, body {
    width: 1200px;
    height: 900px;
    overflow: hidden;
    background: var(--page-bg);
  }
  .canvas {
    position: relative;
    width: 1200px;
    height: 900px;
    display: flex;
    align-items: center;
    justify-content: center;
    gap: 40px;
  }
  .card {
    width: 520px;
    height: 330px;
    border-radius: 26px;
    position: relative;
    display: flex;
    flex-direction: column;
    align-items: center;
    box-shadow: 0 6px 18px rgba(0, 0, 0, 0.12);
  }
  .card--front {
    background: radial-gradient(ellipse at 50% 42%, var(--mint-light) 0%, var(--mint) 60%);
    color: var(--ink);
    padding-top: 108px;
  }
  .name {
    font-family: "Almendra", serif;
    font-weight: 700;
    font-size: 54px;
    line-height: 1;
    letter-spacing: 0.5px;
  }
  .role {
    font-family: "Poiret One", sans-serif;
    font-size: 17px;
    letter-spacing: 7px;
    margin-top: 4px;
  }
  .contact {
    font-family: "Poiret One", sans-serif;
    font-size: 17px;
    letter-spacing: 2.5px;
    text-align: center;
    line-height: 1.45;
    margin-top: 64px;
  }
  .card--back {
    background: radial-gradient(ellipse at 50% 50%, var(--card-dark) 0%, var(--card-dark-edge) 85%);
    justify-content: center;
    gap: 18px;
  }
  .mark-circle {
    width: 110px;
    height: 110px;
    border-radius: 50%;
    background: var(--mint);
    border: 3px solid #e7f5ee;
  }
  .mark-name {
    font-family: "Almendra", serif;
    font-weight: 700;
    font-size: 26px;
    color: var(--mint);
  }
</style>
</head>
<body>
  <main class="canvas">
    <section class="card card--front" aria-label="Card front">
      <h1 class="name">Rosalind Parfrey</h1>
      <p class="role">Wardrobe Stylist</p>
      <p class="contact">
        <span class="contact-phone">0218467193</span><br>
        <span class="contact-email">rosaparfrey@mailbox-example.co.nz</span>
      </p>
    </section>
    <section class="card card--back" aria-label="Card back">
      <div class="mark-circle"></div>
      <p class="mark-name">Rosalind Parfrey</p>
    </section>
  </main>
</body>
</html>
```